Insurance Agency website design for Brellow Cover Insurance, LP

Build a website for Brellow Cover Insurance, LP which sells Homeowners, Auto, Renters, Condo, Flood, Disability, Life, Umbrella, and health insurance. We need the coolest insurance agency website out there to get quotes, contact us, or get additional information. Please list the following insurance companies we work with: Varnix, Ostle, Meridale Mutual, Quillor, Dunmarrow, KGZ, and Pellwick.

Make a design similar to https://www.fernagentry.com/

Selling personal insurance policies

```html
<!DOCTYPE html>
<html lang="en">
<head>
<meta charset="utf-8">
<title>Brellow Cover Insurance</title>
<link rel="stylesheet" href="https://fonts.googleapis.com/css2?family=Roboto+Slab:wght@500;700&family=Roboto:wght@400;500&family=Poppins:wght@400;500;600&display=swap">
<style>
:root{
  --navy:#0c0a8f;
  --navy-dark:#07067a;
  --orange:#f26a1b;
  --ink:#1c1c2a;
  --muted:#444;
  --card-line:#d6d6de;
  --soft:#f1f1f3;
  --contact-bg:#dde8f1;
  --white:#fff;
}
*{margin:0;padding:0;box-sizing:border-box}
html,body{width:1200px;height:3639px;overflow:hidden}
body{font-family:"Roboto",sans-serif;color:var(--ink);background:var(--white);position:relative}
.slab{font-family:"Roboto Slab",serif;font-weight:700}
.abs{position:absolute}
.btn{position:absolute;background:var(--orange);color:var(--white);font-family:"Roboto Slab",serif;font-weight:700;font-size:15px;border-radius:22px;display:flex;align-items:center;justify-content:center;letter-spacing:.3px}
.heading{position:absolute;left:0;width:1200px;text-align:center;font-family:"Roboto Slab",serif;font-weight:700;font-size:38px;color:var(--navy)}
.heading .accent,.accent{color:var(--orange)}

/* top bar */
.topbar{top:0;left:0;width:1200px;height:35px;background:var(--navy);color:var(--white);font-size:15px}
.topbar .mail{left:113px;top:8px;display:flex;align-items:center;gap:6px}
.topbar .agent{right:112px;top:8px}

/* nav */
.nav{top:35px;left:0;width:1200px;height:75px;background:var(--white)}
.nav .links{left:110px;top:30px;display:flex;gap:19px;font-size:15px;color:#333}
.nav .links .active{color:var(--navy);text-decoration:underline}
.brand{left:460px;top:26px;font-family:"Roboto Slab",serif;font-weight:700;font-size:21px;color:var(--navy)}
.nav .phone{left:788px;top:28px;display:flex;align-items:center;gap:8px;font-family:"Poppins",sans-serif;font-size:16px}
.nav .phone b{color:var(--orange);font-weight:600}
.nav .phone span{color:var(--navy)}

/* hero */
.hero{top:110px;left:0;width:1200px;height:600px;background:linear-gradient(90deg,#f6f2ef 0%,#f3e6dc 45%,#e9b48a 70%,#d88a55 100%)}
.hero h1{left:111px;top:170px;font-family:"Roboto Slab",serif;font-weight:700;font-size:44px;line-height:57px;color:var(--navy)}
.hero p{left:110px;top:290px;width:440px;font-size:14px;line-height:23px;color:#222}

/* services */
.svc-card{position:absolute;top:909px;width:197px;height:195px;border:2px solid var(--card-line);border-radius:14px;background:var(--white);text-align:center}
.svc-card svg{margin-top:26px}
.svc-card .label{font-family:"Roboto Slab",serif;font-weight:700;font-size:22px;line-height:30px;color:var(--navy)}

/* about */
.about{top:1265px;left:0;width:1200px;height:557px;background:linear-gradient(90deg,#c9c3bd 0%,#b8aea4 35%,#6b70b8 55%,#1b19a0 75%,var(--navy) 100%)}
.about h2{left:680px;top:113px;font-family:"Roboto Slab",serif;font-weight:700;font-size:35px;line-height:44px;color:var(--white)}
.about p{left:680px;width:450px;font-size:15px;line-height:26px;color:var(--white)}

/* clients */
.client{position:absolute;top:1984px;width:181px;height:73px;border:2px solid var(--card-line);border-radius:12px;display:flex;align-items:center;justify-content:center;font-family:"Poppins",sans-serif;font-weight:500;font-size:19px;color:var(--navy)}

/* testimonials */
.testi{position:absolute;top:2247px;width:310px;height:247px;border-radius:20px;background:var(--soft);text-align:center;font-family:"Poppins",sans-serif;padding:28px 24px 0}
.testi.featured{background:var(--white);border:2px solid #3b4cc0}
.testi p{font-size:15.5px;line-height:28px;color:#222}
.testi .who{margin-top:12px;font-size:15px;font-weight:600;color:#3b4cc0;line-height:18px}
.testi .role{font-size:15px;color:#222;line-height:20px}
.testi .stars{color:var(--orange);font-size:13px;letter-spacing:1px;margin-top:4px}

/* contact */
.contact{top:2614px;left:0;width:1200px;height:756px;background:var(--contact-bg)}
.field{position:absolute;background:var(--white);border:2px solid #cfd6e0;border-radius:6px;font-family:"Roboto Slab",serif;font-weight:500;font-size:20px;color:#444;padding:15px 27px}

/* cta */
.cta{top:3275px;left:112px;width:976px;height:191px;background:var(--navy-dark)}
.cta h3{left:36px;top:50px;font-family:"Roboto Slab",serif;font-weight:700;font-size:32px;line-height:48px;color:var(--white)}

/* footer */
.footer-links{left:598px;top:3522px;display:flex;gap:34px;font-size:15px;color:#222}
.copy{left:598px;top:3557px;font-size:14px;color:#333}
</style>
</head>
<body>

<div class="abs topbar">
  <div class="abs mail">
    <svg width="15" height="11" viewBox="0 0 15 11"><rect x="0.5" y="0.5" width="14" height="10" fill="#fff"/><path d="M1 1l6.5 5 6.5-5" stroke="#0c0a8f" fill="none"/></svg>
    <span>| info@BrellowCoverInsurance.com</span>
  </div>
  <div class="abs agent">Are you an independent agent? Sign Up | Log In</div>
</div>

<div class="abs nav">
  <div class="abs links"><span class="active">Home</span><span>About Us</span><span>Services</span><span>Reviews</span></div>
  <div class="abs brand">BRELLOW COVER INSURANCE</div>
  <div class="abs phone">
    <svg width="22" height="22" viewBox="0 0 24 24"><path fill="#f26a1b" d="M6.6 10.8a15.1 15.1 0 0 0 6.6 6.6l2.2-2.2c.3-.3.7-.4 1-.2 1.1.4 2.3.6 3.6.6.6 0 1 .4 1 1V20c0 .6-.4 1-1 1C10.6 21 3 13.4 3 4c0-.6.4-1 1-1h3.5c.6 0 1 .4 1 1 0 1.3.2 2.5.6 3.6.1.3 0 .7-.2 1z"/></svg>
    <b>Talk to an agent :</b><span>(612) 555-0148</span>
  </div>
</div>

<section class="abs hero" role="img" aria-label="Hand stacking wooden blocks printed with shield, family, home, savings, medical kit and car icons">
  <h1 class="abs"><span class="accent">WELCOME TO </span>BRELLOW<br>COVER INSURANCE</h1>
  <p class="abs">Lorem ipsum dolor sit amet, consectetur adipiscing elit, sed do eiusmod tempor incididunt ut labore et dolore magna aliqua. Quis ipsum suspendisse ultrices gravida.</p>
  <div class="btn" style="left:111px;top:382px;width:158px;height:40px">GET A QUOTE</div>
</section>

<h2 class="heading" style="top:784px"><span class="accent">OUR</span> SERVICES</h2>

<div class="svc-card" style="left:130px">
  <svg width="78" height="78" viewBox="0 0 78 78" fill="none" stroke="#f26a1b" stroke-width="2.5" stroke-linejoin="round"><path d="M14 32L39 12l25 20"/><path d="M20 28v20h38V28"/><path d="M39 22l10 4v7c0 6-4 10-10 12-6-2-10-6-10-12v-7z"/><path d="M34 32l4 4 6-6"/><path d="M6 52h12l10 6h12a3 3 0 0 1 0 6H26"/><path d="M40 64l22-10a4 4 0 0 1 4 6L44 72H6"/></svg>
  <div class="label">Property<br>Insurance</div>
</div>
<div class="svc-card" style="left:376px">
  <svg width="90" height="78" viewBox="0 0 90 78" fill="none" stroke="#f26a1b" stroke-width="2.5" stroke-linejoin="round"><path d="M6 50v-10l8-4 10-12h36l12 12 12 4v10z"/><path d="M28 26v10M46 26v10M16 36h56"/><circle cx="22" cy="52" r="7" fill="#fff"/><circle cx="68" cy="52" r="7" fill="#fff"/></svg>
  <div class="label" style="margin-top:4px">Auto</div>
</div>
<div class="svc-card" style="left:622px">
  <svg width="78" height="78" viewBox="0 0 78 78" fill="none" stroke="#f26a1b" stroke-width="2.5" stroke-linejoin="round"><circle cx="42" cy="26" r="8"/><path d="M42 34v14M42 40h5M42 45h4"/><path d="M54 10v24c0 6-4 10-10 12"/><path d="M8 62l12-12h14l8 4h-12M20 70l10-6h16l14-12"/></svg>
  <div class="label" style="margin-top:4px">Renters</div>
</div>
<div class="svc-card" style="left:868px">
  <svg width="78" height="78" viewBox="0 0 78 78" fill="none" stroke="#f26a1b" stroke-width="2.5" stroke-linejoin="round"><path d="M39 40C26 30 22 24 24 17a8 8 0 0 1 15-2 8 8 0 0 1 15 2c2 7-2 13-15 23z"/><path d="M39 18v10M34 23h10"/><path d="M10 30l6 20 12 10v10M68 30l-6 20-12 10v10"/><path d="M18 44l8 8M60 44l-8 8"/></svg>
  <div class="label">Health<br>Insurance</div>
</div>

<div class="btn" style="left:530px;top:1139px;width:140px;height:40px">VIEW MORE</div>

<section class="abs about" role="img" aria-label="Smiling family sitting on moving boxes in front of a brick wall with a house outline">
  <h2 class="abs">ABOUT BRELLOW<br>COVER INSURANCE</h2>
  <p class="abs" style="top:214px">Brellow Cover Insurance is a full-service, independent insurance agency with over three decades of experience in delivering comprehensive insurance solutions to individuals.</p>
  <p class="abs" style="top:300px">We proudly offer a diverse portfolio of products from more than 20 of the most reputable and financially secure companies in the industry.</p>
  <div class="btn" style="left:680px;top:395px;width:140px;height:40px">READ MORE</div>
</section>

<h2 class="heading" style="top:1896px"><span class="accent">OUR</span> CLIENTS</h2>
<div class="client" style="left:109px">Varnix</div>
<div class="client" style="left:309px">Meridale Mutual</div>
<div class="client" style="left:509px">Dunmarrow</div>
<div class="client" style="left:709px">KGZ</div>
<div class="client" style="left:910px">Pellwick</div>

<h2 class="heading" style="top:2154px"><span class="accent">OUR</span> TESTIMONIALS</h2>
<div class="testi" style="left:112px">
  <p>Lorem ipsum dolor sit amet, consectetur adipiscing elit, sed do eiusmod tempor incididunt ut labore et dolore magna aliqua.</p>
  <div class="who">– Sarah T.,</div><div class="role">Small Business Owner</div><div class="stars">★★★★★</div>
</div>
<div class="testi featured" style="left:444px">
  <p>Lorem ipsum dolor sit amet, consectetur adipiscing elit, sed do eiusmod tempor incididunt ut labore et dolore magna</p>
  <div class="who">– Michael R.</div><div class="role">Enterprise Manager</div><div class="stars">★★★★★</div>
</div>
<div class="testi" style="left:779px">
  <p>Lorem ipsum dolor sit amet, consectetur adipiscing elit, sed do eiusmod tempor incididunt ut labore et dolore magna aliqua.</p>
  <div class="who">– Lisa K.,</div><div class="role">Digital Marketer</div><div class="stars">★★★★★</div>
</div>

<section class="abs contact">
  <h2 class="heading" style="top:75px"><span class="accent">CONTACT</span> US</h2>
  <div class="field" style="left:162px;top:158px;width:430px;height:64px">First Name</div>
  <div class="field" style="left:608px;top:158px;width:430px;height:64px">Last Name</div>
  <div class="field" style="left:162px;top:237px;width:430px;height:64px">Phone Number</div>
  <div class="field" style="left:608px;top:237px;width:430px;height:64px">Email</div>
  <div class="field" style="left:162px;top:318px;width:876px;height:154px">Message</div>
  <div class="btn" style="left:530px;top:492px;width:140px;height:40px">SUBMIT</div>
</section>

<section class="abs cta">
  <h3 class="abs">HAVE QUESTIONS?<br>PLEASE CONTACT US TODAY</h3>
  <div class="btn" style="left:688px;top:65px;width:251px;height:40px">GET IN TOUCH WITH US</div>
</section>

<div class="abs brand" style="left:170px;top:3534px;font-size:23px">BRELLOW COVER INSURANCE</div>
<div class="abs footer-links"><span>Home</span><span>About Us</span><span>Services</span><span>Reviews</span><span>Contact Us</span></div>
<div class="abs copy">© 2025 Brellow Cover Insurance LP | All rights reserved.</div>

</body>
</html>
```